Business Card for a New Zealand IT Startup

I need a business card for VELTA Holdings. We are a young startup based in New Zealand working in internet marketing and web development. The design should have some element connected to New Zealand, such as wave, koru or silver fern, just don't use a kiwi bird.

```html
<!DOCTYPE html>
<html lang="en">
<head>
<meta charset="utf-8">
<title>VELTA Holdings — Business Card</title>
<link href="https://fonts.googleapis.com/css2?family=Montserrat:wght@400;500;700&display=swap" rel="stylesheet">
<style>
  :root {
    --brand-blue: #1f73c4;
    --accent-orange: #f0622a;
    --card-white: #ffffff;
    --backdrop: #e9e6e1;
    --text-light: #ffffff;
  }
  html, body {
    margin: 0;
    padding: 0;
    width: 1200px;
    height: 1040px;
    overflow: hidden;
    background: var(--backdrop);
    font-family: "Montserrat", sans-serif;
  }
  .canvas { position: relative; width: 1200px; height: 1040px; }
  .card {
    position: absolute;
    width: 640px;
    height: 366px;
    border-radius: 22px;
    overflow: hidden;
    box-shadow: 0 8px 22px rgba(0,0,0,0.18);
  }
  .card-front { left: 70px; top: 80px; background: var(--card-white); }
  .card-back { left: 490px; top: 590px; background: var(--brand-blue); }
  .card-art { position: absolute; inset: 0; width: 100%; height: 100%; }

  .wordmark {
    position: absolute;
    color: var(--brand-blue);
    font-weight: 700;
    text-transform: uppercase;
  }
  .front-wordmark { left: 52px; top: 52px; }
  .wordmark-name { display: block; font-size: 44px; letter-spacing: 4px; line-height: 1; }
  .wordmark-sub { display: block; font-size: 15px; letter-spacing: 11px; margin-top: 8px; color: var(--accent-orange); }

  .holder {
    position: absolute;
    right: 40px;
    top: 118px;
    text-align: right;
    color: var(--text-light);
  }
  .holder-name { font-size: 20px; font-weight: 500; letter-spacing: 0.5px; text-transform: uppercase; }
  .holder-title { font-size: 13px; letter-spacing: 0.5px; text-transform: uppercase; margin-top: 4px; }

  .contact {
    position: absolute;
    left: 274px;
    bottom: 24px;
    color: var(--text-light);
    font-size: 13px;
    line-height: 1.55;
  }
  .contact-address { margin-bottom: 4px; }
  .contact-row { display: flex; align-items: center; gap: 8px; }
  .contact-row svg { width: 12px; height: 12px; flex: none; }

  .back-wordmark {
    position: absolute;
    left: 0; right: 0; top: 96px;
    text-align: center;
    color: var(--text-light);
    font-weight: 700;
    text-transform: uppercase;
  }
  .back-wordmark .wordmark-name { font-size: 62px; letter-spacing: 6px; }
  .back-wordmark .wordmark-sub { font-size: 20px; letter-spacing: 16px; margin-top: 10px; color: var(--text-light); }
  .back-web {
    position: absolute;
    left: 0; right: 0; top: 222px;
    text-align: center;
    color: var(--text-light);
    font-size: 13px;
    letter-spacing: 5px;
  }
</style>
</head>
<body>
<main class="canvas">

  <section class="card card-front" aria-label="Business card front">
    <svg class="card-art" viewBox="0 0 640 366" preserveAspectRatio="none" aria-hidden="true">
      <path class="wave-accent" d="M 326 0 C 392 50, 362 140, 262 185 C 180 222, 134 280, 112 366 L 130 366 C 150 280, 190 222, 270 185 C 370 140, 400 50, 330 0 Z" fill="var(--accent-orange)"/>
      <path class="wave-band" d="M 330 0 C 400 50, 370 140, 270 185 C 190 222, 150 280, 130 366 L 640 366 L 640 0 Z" fill="var(--brand-blue)"/>
      <path class="wave-line" d="M 360 0 C 410 35, 415 75, 398 104" fill="none" stroke="var(--text-light)" stroke-width="1.4" opacity="0.85"/>
    </svg>

    <div class="wordmark front-wordmark">
      <span class="wordmark-name">Velta</span>
      <span class="wordmark-sub">Holdings</span>
    </div>

    <div class="holder">
      <div class="holder-name">Aroha Mitchell</div>
      <div class="holder-title">CEO/Founder</div>
    </div>

    <div class="contact">
      <div class="contact-address">412 Harbour Street<br>Wellington 6011, New Zealand</div>
      <div class="contact-row">
        <svg viewBox="0 0 16 16" aria-hidden="true"><path d="M4 1 L6.5 4.5 L5 6.5 C6 8.5 7.5 10 9.5 11 L11.5 9.5 L15 12 L13 15 C7 14.5 1.5 9 1 3 Z" fill="var(--text-light)"/></svg>
        <span>021 555 0147</span>
      </div>
      <div class="contact-row">
        <svg viewBox="0 0 16 16" aria-hidden="true"><rect x="4" y="1" width="8" height="14" rx="1.5" fill="none" stroke="var(--text-light)" stroke-width="1.6"/></svg>
        <span>022 555 0193</span>
      </div>
      <div class="contact-row">
        <svg viewBox="0 0 16 16" aria-hidden="true"><rect x="1" y="3" width="14" height="10" fill="var(--text-light)"/><path d="M1 3 L8 9 L15 3" fill="none" stroke="var(--brand-blue)" stroke-width="1.4"/></svg>
        <span>aroha@veltaholdings.com</span>
      </div>
    </div>
  </section>

  <section class="card card-back" aria-label="Business card back">
    <div class="back-wordmark">
      <span class="wordmark-name">Velta</span>
      <span class="wordmark-sub">Holdings</span>
    </div>
    <div class="back-web">veltaholdings.com</div>
  </section>

</main>
</body>
</html>
```